Oil and Gas Exploration and Production company needs a business card design

We need a business card design using our logo and colors in the logo. We want a mainstream design.

```html
<!DOCTYPE html>
<html lang="en">
<head>
<meta charset="utf-8">
<title>Norda Oil &amp; Gas – Business Card</title>
<link href="https://fonts.googleapis.com/css2?family=Roboto:wght@400;500;700&family=Roboto+Condensed:wght@700&display=swap" rel="stylesheet">
<style>
  :root {
    --backdrop: #2a2a2b;
    --card-light: #f7f7f5;
    --card-dark: #1a1a1b;
    --ink: #111111;
    --gold: #c8962a;
    --white: #f4f4f4;
    --muted: #555555;
    --rule: #8a8a8a;
  }
  * { margin: 0; padding: 0; box-sizing: border-box; }
  html, body {
    width: 1200px; height: 900px; overflow: hidden;
    background: var(--backdrop);
    font-family: "Roboto", Arial, sans-serif;
  }
  .stage { position: relative; width: 1200px; height: 900px; }
  .card {
    position: absolute; left: 280px; width: 640px; height: 360px;
    box-shadow: 0 12px 30px rgba(0,0,0,.45);
  }
  .card-front { top: 70px; background: var(--card-light); }
  .card-back { top: 470px; background: var(--card-dark); color: var(--white); }

  .brand {
    position: absolute; top: 112px; left: 0; right: 0;
    display: flex; align-items: center; justify-content: center; gap: 14px;
  }
  .brand-dot { width: 46px; height: 46px; border-radius: 50%; background: var(--gold); }
  .brand-name {
    font-weight: 700; font-size: 62px; color: var(--ink); letter-spacing: -1px; line-height: 1;
  }
  .front-web {
    position: absolute; top: 248px; left: 0; right: 0; text-align: center;
    font-size: 15px; letter-spacing: 6px; color: var(--muted);
  }

  .person { position: absolute; top: 128px; right: 382px; text-align: right; }
  .person-name {
    font-family: "Roboto Condensed", Arial, sans-serif; font-weight: 700;
    font-size: 36px; line-height: 1; letter-spacing: .5px; color: var(--white);
  }
  .person-role { margin-top: 6px; font-size: 16px; font-weight: 500; color: var(--gold); letter-spacing: .5px; }
  .divider { position: absolute; left: 278px; top: 105px; width: 1px; height: 110px; background: var(--rule); }
  .contacts { position: absolute; left: 300px; top: 110px; list-style: none; }
  .contacts li { display: flex; align-items: center; gap: 10px; height: 21px; font-size: 16px; }
  .contacts svg { width: 14px; height: 14px; fill: var(--white); flex: none; }
  .address {
    position: absolute; left: 40px; top: 288px; display: flex; align-items: center; gap: 8px; font-size: 17px;
  }
  .address svg { width: 14px; height: 18px; fill: var(--white); }
</style>
</head>
<body>
<main class="stage">
  <section class="card card-front">
    <div class="brand">
      <span class="brand-dot"></span>
      <span class="brand-name">Norda Oil &amp; Gas</span>
    </div>
    <p class="front-web">www.nordaoilgas.com</p>
  </section>

  <section class="card card-back">
    <div class="person">
      <h1 class="person-name">DANIEL REYES</h1>
      <p class="person-role">CEO/FOUNDER</p>
    </div>
    <span class="divider"></span>
    <ul class="contacts">
      <li><svg viewBox="0 0 24 24"><path d="M6.6 10.8a15 15 0 0 0 6.6 6.6l2.2-2.2c.3-.3.7-.4 1-.2 1.1.4 2.3.6 3.6.6.6 0 1 .4 1 1V20c0 .6-.4 1-1 1A17 17 0 0 1 3 4c0-.6.4-1 1-1h3.5c.6 0 1 .4 1 1 0 1.3.2 2.5.6 3.6.1.3 0 .7-.2 1z"/></svg>555 214 7730</li>
      <li><svg viewBox="0 0 24 24"><path d="M7 1h10a2 2 0 0 1 2 2v18a2 2 0 0 1-2 2H7a2 2 0 0 1-2-2V3a2 2 0 0 1 2-2zm0 3v14h10V4z"/></svg>555 318 4062</li>
      <li><svg viewBox="0 0 24 24"><path d="M6 2h12v5H6zM4 8h16a2 2 0 0 1 2 2v7h-4v5H6v-5H2v-7a2 2 0 0 1 2-2zm4 8v4h8v-4z"/></svg>555 902 1185</li>
      <li><svg viewBox="0 0 24 24"><path d="M2 5h20v14H2zm2 2v.5l8 5 8-5V7z"/></svg>info@nordaoilgas.com</li>
      <li><svg viewBox="0 0 24 24"><circle cx="12" cy="12" r="10"/></svg>www.nordaoilgas.com</li>
    </ul>
    <p class="address">
      <svg viewBox="0 0 14 18"><path d="M7 0a7 7 0 0 1 7 7c0 5-7 11-7 11S0 12 0 7a7 7 0 0 1 7-7zm0 4a3 3 0 1 0 0 6 3 3 0 0 0 0-6z"/></svg>
      4120 Birch Ridge Road, Anchorage, Alaska 99508
    </p>
  </section>
</main>
</body>
</html>
```